Professional Website for Leading Global Private Equity Real Estate Company

The company is a leading global Private Equity Real Estate (PERE). We need a homepage design, an inner page design, and color/font tweaks to the logo (color should be more soothing than current blue used in the logo). The logo website should project the company as global, professional, experienced, trustworthy, accessible, YOUNG, DYNAMIC, hi-tech. PLEASE SEE the attached Design Brief Word Doc for details.

Target Market(s)

institional investors and wealthy private individuals

Industry/Entity Type

Finance

Number of Pages Required

2 page

Font styles to use
Sans Serif
Other font styles liked:
• either like in https://www.ferndalequay.com/ or like in presentations (Montserrat Black & Montserrat Light, Century Gothic, Blair ITC, Almoni Neue DL 4.0 AAA Medium, Almoni DL AAA)

Requirements
Must have
• new color palette that is NOT based on current logo. they want a more soothing color palette than the blue in that logo. the new color palette should project: global, professional, experienced, trustworthy, accessible, YOUNG, DYNAMIC, hi-tech.
Nice to have
• the likes these sites: https://www.ferndalequay.com/ and https://www.tvr.law/

```html
<!DOCTYPE html>
<html lang="en">
<head>
<meta charset="utf-8">
<title>Veltara Real Estate</title>
<link rel="stylesheet" href="https://fonts.googleapis.com/css2?family=Montserrat:wght@400;500;600;700&display=swap">
<style>
:root{
  --teal:#1fc2b5;
  --teal-dark:#17a99d;
  --navy:#0d1b4c;
  --gold:#c79b45;
  --ink:#222a3a;
  --muted:#3c4150;
  --line:#e3e6ec;
  --soft:#f4f5f8;
  --card:#ececef;
  --white:#ffffff;
}
*{box-sizing:border-box;margin:0;padding:0}
html,body{width:1200px;height:4332px;overflow:hidden}
body{position:relative;background:var(--white);font-family:"Montserrat",sans-serif;color:var(--ink)}
.abs{position:absolute}

/* header */
.top-email{left:161px;top:26px;display:flex;align-items:center;gap:8px;font-size:14px;font-weight:500}
.icon-dot{width:28px;height:28px;border-radius:50%;background:var(--teal);display:flex;align-items:center;justify-content:center}
.brand{display:flex;align-items:center;gap:10px;font-weight:700;letter-spacing:4px;color:var(--navy)}
.brand-dot{border-radius:50%;background:var(--gold)}
.header-brand{left:505px;top:20px;font-size:28px}
.header-brand .brand-dot{width:34px;height:34px}
.login{left:966px;top:26px;display:flex;align-items:center;gap:8px;font-size:14px;font-weight:600}
.header-rule{left:0;top:79px;width:1200px;height:1px;background:var(--line)}
.nav{left:0;top:80px;width:1200px;height:57px}
.nav a{position:absolute;top:19px;font-size:13px;font-weight:600;color:var(--ink);text-decoration:none;transform:translateX(-50%)}
.nav a.active{color:var(--teal)}
.nav-underline{left:160px;top:132px;width:42px;height:5px;background:var(--teal)}

/* hero */
.hero{left:0;top:137px;width:1200px;height:435px;background:linear-gradient(180deg,#6a7c8c 0%,#4e6373 45%,#2f4a5c 75%,#3b4a52 100%)}
.hero-title{left:0;top:118px;width:1200px;text-align:center;color:var(--white);font-size:47px;font-weight:700;line-height:60px;text-shadow:0 2px 8px rgba(0,0,0,.35)}

/* buttons */
.btn{display:inline-flex;align-items:center;gap:12px;height:44px;padding:0 22px 0 7px;border-radius:22px;background:var(--teal);color:var(--white);font-size:13.5px;font-weight:600;white-space:nowrap}
.btn .dot{width:32px;height:32px;border-radius:50%;background:var(--white)}
.btn.gold{background:var(--gold)}
.hero .btn{position:absolute;left:537px;top:260px}

/* common text */
.h2{font-size:35px;font-weight:700;color:var(--navy)}
.body-copy p{font-size:12px;line-height:21.5px;color:var(--muted);margin-bottom:5px}

/* about */
.about-title{left:163px;top:680px}
.about-copy{left:163px;top:730px;width:410px}
.about-copy p{font-size:11.3px;line-height:21.5px}
.about-btn{left:163px;top:1048px}
.stat{width:198px;height:190px;border-radius:14px;background:var(--card);text-align:center;padding-top:14px}
.stat .num{font-size:33px;font-weight:700;color:var(--navy);line-height:40px}
.stat .unit{font-size:22px;font-weight:500;color:var(--navy);line-height:28px}
.stat svg{margin:12px auto 6px;display:block}
.stat .label{font-size:13px;font-weight:500;color:var(--ink)}

/* platforms */
.platforms{left:0;top:1206px;width:1200px;height:722px;background:linear-gradient(160deg,#f6f7f9 0%,#eef0f3 100%)}
.platforms-title{left:0;top:70px;width:1200px;text-align:center}
.tabs{left:163px;top:143px;display:flex;gap:4px}
.tab{position:relative;width:172px;height:171px;border:1px solid #d8dbe2;border-radius:10px;background:var(--white);display:flex;flex-direction:column;align-items:center;justify-content:center;gap:6px}
.tab .tab-dot{width:44px;height:44px;border-radius:50%;background:var(--teal)}
.tab .tab-name{font-size:19px;font-weight:700;letter-spacing:3px;color:var(--navy)}
.tab .tab-sub{font-size:13px;color:var(--teal);letter-spacing:.5px}
.tab.active{background:var(--teal);border-color:var(--teal)}
.tab.active .tab-dot{background:var(--white)}
.tab.active .tab-name,.tab.active .tab-sub{color:var(--white)}
.tab.active::after{content:"";position:absolute;left:76px;bottom:-12px;border-left:10px solid transparent;border-right:10px solid transparent;border-top:12px solid var(--teal)}
.debt-photo{left:163px;top:366px;width:412px;height:283px;border-radius:14px;background:linear-gradient(135deg,#c9ccd0 0%,#9ea4aa 50%,#5d6166 100%)}
.debt-title{left:625px;top:378px;font-size:24px;font-weight:700;color:var(--navy)}
.debt-copy{left:626px;top:418px;width:410px}
.debt-copy p{font-size:13px;line-height:25px;margin-bottom:6px}
.debt-btn{left:626px;top:588px}

/* edge */
.edge-title{left:163px;top:2075px}
.edge-copy{left:163px;top:2128px;width:410px}
.edge-btn{left:163px;top:2304px}
.edge-photo{left:625px;top:2013px;width:413px;height:406px;border-radius:50%;background:linear-gradient(135deg,#d7dde0 0%,#6e8795 50%,#233a56 100%)}

/* newsletter */
.newsletter{left:161px;top:2500px;width:877px;height:290px;border-radius:22px;background:var(--soft);text-align:center}
.newsletter .h2{margin-top:65px}
.newsletter .lead{font-size:13px;color:var(--muted);margin-top:16px}
.subscribe{position:absolute;left:232px;top:171px;width:413px;height:44px;border:1px solid #c9ccd4;border-radius:22px;background:var(--white)}
.subscribe span{position:absolute;left:24px;top:14px;font-size:11px;color:#9aa0ab}
.subscribe .go{position:absolute;right:3px;top:3px;width:62px;height:36px;border-radius:18px;background:var(--teal);display:flex;align-items:center;justify-content:center}

/* responsibility */
.resp-photo{left:161px;top:2868px;width:414px;height:408px;border-radius:50%;background:linear-gradient(135deg,#e2e3e5 0%,#a9adb3 45%,#3e444c 100%)}
.resp-title{left:632px;top:2930px}
.resp-copy{left:628px;top:2983px;width:410px}
.resp-btn{left:628px;top:3159px}

/* enquiry */
.enquiry-band{left:0;top:3787px;width:1200px;height:500px;background:#f6f7f9}
.enquiry{left:161px;top:3367px;width:877px;height:540px;background:var(--white);box-shadow:0 6px 26px rgba(20,30,60,.08);text-align:center}
.enquiry .h2{margin-top:60px}
.enquiry .lead{width:620px;margin:16px auto 0;font-size:13px;line-height:25px;color:var(--muted)}
.field{position:absolute;border:1px solid #dcdfe5;background:var(--white);font-size:12px;color:#9aa0ab;text-align:left;padding:15px 16px}
.enquiry .btn{position:absolute;left:366px;top:416px}
.corner{right:0;bottom:0}

/* footer */
.footer-brand{left:161px;top:3990px;font-size:26px}
.footer-brand .brand-dot{width:32px;height:32px}
.footer-about{left:163px;top:4040px;width:220px;font-size:13px;line-height:24.5px;color:var(--ink)}
.fcol h4{font-size:15px;font-weight:600;color:var(--navy);margin-bottom:14px}
.fcol li{list-style:none;font-size:13px;line-height:29.6px;color:var(--ink)}
.contact-row{display:flex;gap:12px;margin-bottom:12px}
.contact-row b{display:block;font-size:13px;font-weight:600;color:var(--navy)}
.contact-row span{font-size:13px;line-height:22px}
.bottom-bar{left:0;top:4280px;width:1200px;height:52px;background:var(--navy);color:var(--white)}
.bottom-bar p{position:absolute;left:163px;top:18px;font-size:12.5px}
.socials{position:absolute;right:162px;top:12px;display:flex;gap:8px}
.socials span{width:28px;height:28px;border:1.5px solid var(--white);border-radius:50%}
</style>
</head>
<body>

<header>
  <div class="abs top-email"><span class="icon-dot"><svg width="14" height="10" viewBox="0 0 14 10"><rect x="0.7" y="0.7" width="12.6" height="8.6" fill="none" stroke="#fff" stroke-width="1.4"/><path d="M1 1l6 5 6-5" fill="none" stroke="#fff" stroke-width="1.4"/></svg></span>info@veltara.com</div>
  <div class="abs brand header-brand"><span class="brand-dot"></span>VELTARA</div>
  <div class="abs login"><span class="icon-dot"><svg width="12" height="14" viewBox="0 0 12 14"><circle cx="6" cy="4" r="3" fill="none" stroke="#fff" stroke-width="1.4"/><path d="M1 13c0-3 2-5 5-5s5 2 5 5" fill="none" stroke="#fff" stroke-width="1.4"/></svg></span>Login</div>
  <div class="abs header-rule"></div>
  <nav class="abs nav">
    <a class="active" style="left:181px">Home</a>
    <a style="left:331px">About Us</a>
    <a style="left:513px">Our Businesses</a>
    <a style="left:694px">Investors</a>
    <a style="left:843px">News</a>
    <a style="left:999px">Contact Us</a>
  </nav>
  <div class="abs nav-underline"></div>
</header>

<section class="abs hero" role="img" aria-label="Aerial photograph of a city skyline along a river">
  <h1 class="abs hero-title">We Are Leading Global Private<br>Equity Real Estate Firm</h1>
  <span class="btn gold"><span class="dot"></span>About Us</span>
</section>

<section>
  <h2 class="abs h2 about-title">About Us</h2>
  <div class="abs body-copy about-copy">
    <p>Veltara Consumer Products, of the Orvan Group, which was founded in 1951, is the longest-standing and leading company in Israel in the area of home electrical appliances and air conditioning.</p>
    <p>The Company is engaged in the production, import, export, sales, distribution, marketing and provision of services for a broad variety of consumer electrical appliances.</p>
    <p>The Company has an annual sales turnover of NIS 2.49 billion and it employs around 1,600 employees.</p>
    <p>The Company owns two chains specializing in the sale of some of the leading electric products in Israel: Norvel Electric and Halden Home.</p>
    <p>Veltara sells and markets a variety of leading products and brands, ranging from the affordable to luxury brands.</p>
  </div>
  <span class="abs btn about-btn"><span class="dot"></span>Read More</span>

  <div class="abs stat" style="left:628px;top:667px">
    <div class="num">4.6</div><div class="unit">NIS Bilion</div>
    <svg width="40" height="40" viewBox="0 0 40 40" fill="none" stroke="#222a3a" stroke-width="1.5"><path d="M15 10h10l-3 5h-4z"/><path d="M18 15c-8 4-10 20 2 20s10-16 2-20"/><text x="17" y="29" font-size="10" fill="#222a3a" stroke="none">$</text><rect x="27" y="26" width="10" height="9"/></svg>
    <div class="label">Annual Revenues</div>
  </div>
  <div class="abs stat" style="left:840px;top:690px">
    <div class="num">265.59</div><div class="unit">NIS Million</div>
    <svg width="40" height="40" viewBox="0 0 40 40" fill="none" stroke="#222a3a" stroke-width="1.5"><circle cx="12" cy="10" r="5"/><circle cx="28" cy="10" r="5"/><circle cx="20" cy="18" r="5"/><path d="M20 23v8M12 15l4 8M28 15l-4 8M10 34h20"/></svg>
    <div class="label">Annual Operating Income</div>
  </div>
  <div class="abs stat" style="left:628px;top:880px">
    <div class="num">164</div><div class="unit">NIS Million</div>
    <svg width="40" height="40" viewBox="0 0 40 40" fill="none" stroke="#222a3a" stroke-width="1.5"><circle cx="22" cy="10" r="6"/><path d="M4 26h8l6 3h10l6-4M4 32h10l8 2 12-6"/></svg>
    <div class="label">Annual Net Profit</div>
  </div>
  <div class="abs stat" style="left:840px;top:904px">
    <div class="num">1.2</div><div class="unit">NIS Bilion</div>
    <svg width="40" height="40" viewBox="0 0 40 40" fill="none" stroke="#222a3a" stroke-width="1.5"><path d="M20 6l10 8v10H20z"/><path d="M4 26h8l6 3h10M4 32h10l8 2 12-6"/></svg>
    <div class="label">Equity</div>
  </div>
</section>

<section class="abs platforms">
  <h2 class="abs h2 platforms-title">Our Investment Platforms</h2>
  <div class="abs tabs">
    <div class="tab"><span class="tab-dot"></span><span class="tab-name">VELTARA</span><span class="tab-sub">MULTIFAMILY</span></div>
    <div class="tab active"><span class="tab-dot"></span><span class="tab-name">VELTARA</span><span class="tab-sub">DEBT</span></div>
    <div class="tab"><span class="tab-dot"></span><span class="tab-name">VELTARA</span><span class="tab-sub">SINGLE FAMILY</span></div>
    <div class="tab"><span class="tab-dot"></span><span class="tab-name">VELTARA</span><span class="tab-sub">HOSPITALITY</span></div>
    <div class="tab"><span class="tab-dot"></span><span class="tab-name">VELTARA</span><span class="tab-sub">UK</span></div>
  </div>
  <div class="abs debt-photo" role="img" aria-label="Photograph of hands reviewing documents beside laptops"></div>
  <h3 class="abs debt-title">Veltara Debt</h3>
  <div class="abs body-copy debt-copy">
    <p>Lorem ipsum dolor sit amet, consectetuer adipiscing elit, sed diam nonummy nibh euismod tincidunt ut laoreet dolore magna aliquam erat volutpat.</p>
    <p>Lorem ipsum dolor sit amet, consectetuer adipiscing elit, sed diam nonummy lorem ipsum dolor sit amet, consectetuer er adipiscing elit, sed diam nonummy.</p>
  </div>
  <span class="abs btn debt-btn"><span class="dot"></span>Contact Us</span>
</section>

<section>
  <h2 class="abs h2 edge-title">Our Edge</h2>
  <div class="abs body-copy edge-copy">
    <p>Lorem ipsum dolor sit amet, consectetuer adipiscing elit, sed diam nonummy nibh euismod tincidunt ut laoreet dolore magna aliquam erat volutpat.</p>
    <p>Lorem ipsum dolor sit amet, consectetuer adipiscing elit, sed diam nonummy</p>
    <p>Lorem ipsum dolor sit amet, consectetuer adipiscing elit, sed diam nonummy</p>
  </div>
  <span class="abs btn edge-btn"><span class="dot"></span>Investor Information</span>
  <div class="abs edge-photo" role="img" aria-label="Photograph of two businessmen reviewing a chart on a laptop"></div>
</section>

<section class="abs newsletter">
  <h2 class="h2">Newsletter Signup</h2>
  <p class="lead">Lorem ipsum dolor sit amet, consectetuer adipiscing elit, sed diam nonummy</p>
  <div class="subscribe"><span>Enter email id</span><span class="go"><svg width="10" height="14" viewBox="0 0 10 14"><path d="M2 2l5 5-5 5" fill="none" stroke="#fff" stroke-width="2"/></svg></span></div>
</section>

<section>
  <div class="abs resp-photo" role="img" aria-label="Photograph of two businessmen shaking hands across a desk"></div>
  <h2 class="abs h2 resp-title">Our Responsibility</h2>
  <div class="abs body-copy resp-copy">
    <p>Lorem ipsum dolor sit amet, consectetuer adipiscing elit, sed diam nonummy nibh euismod tincidunt ut laoreet dolore magna aliquam erat volutpat.</p>
    <p>Lorem ipsum dolor sit amet, consectetuer adipiscing elit, sed diam nonummy</p>
    <p>Lorem ipsum dolor sit amet, consectetuer adipiscing elit, sed diam nonummy</p>
  </div>
  <span class="abs btn resp-btn"><span class="dot"></span>Read More</span>
</section>

<div class="abs enquiry-band"></div>
<section class="abs enquiry">
  <h2 class="h2">Quick Enquiry</h2>
  <p class="lead">Lorem ipsum dolor sit amet, consectetuer adipiscing elit, sed diam nonummy nibh euismod tincidunt ut laoreet dolore magna aliquam erat volutpat.</p>
  <div class="field" style="left:138px;top:190px;width:293px;height:44px">Name</div>
  <div class="field" style="left:445px;top:190px;width:293px;height:44px">Email</div>
  <div class="field" style="left:138px;top:247px;width:293px;height:44px">Phone</div>
  <div class="field" style="left:445px;top:247px;width:293px;height:44px">Company</div>
  <div class="field" style="left:138px;top:305px;width:600px;height:88px">Message</div>
  <span class="btn"><span class="dot"></span>Get In Touch</span>
  <svg class="abs corner" width="38" height="38" viewBox="0 0 38 38"><path d="M38 0L0 38h38z" fill="#0d1b4c"/></svg>
</section>

<footer>
  <div class="abs brand footer-brand"><span class="brand-dot"></span>VELTARA</div>
  <p class="abs footer-about">Lorem ipsum dolor sit amet gftin consectetuer adipiscing elit, sedr diam nonummy nibh euismodrt tincidunt ut laoreet dolore magn aliquam erat volutpat.</p>
  <div class="abs fcol" style="left:435px;top:4003px">
    <h4>Quick Links</h4>
    <ul><li>Home</li><li>About Us</li><li>Our Businesses</li><li>Investors</li><li>News</li><li>Contact Us</li></ul>
  </div>
  <div class="abs fcol" style="left:609px;top:4003px">
    <h4>Our Businesses</h4>
    <ul><li>Veltara Multifamily</li><li>Veltara Debt</li><li>Veltara Single Family</li><li>Veltara Hospitality</li><li>Veltara UK</li></ul>
  </div>
  <div class="abs fcol" style="left:820px;top:4003px">
    <h4>Contact Details</h4>
    <div class="contact-row"><svg width="16" height="20" viewBox="0 0 16 20"><path d="M8 1a6 6 0 0 0-6 6c0 5 6 12 6 12s6-7 6-12a6 6 0 0 0-6-6z" fill="#1fc2b5"/><circle cx="8" cy="7" r="2.2" fill="#fff"/></svg><div><b>Address</b><span>Street Name, City - 987 654</span></div></div>
    <div class="contact-row"><svg width="16" height="18" viewBox="0 0 16 18"><path d="M3 1l3 4-2 2c1 3 3 5 6 6l2-2 4 3-2 3C7 17 0 10 1 3z" fill="#1fc2b5"/></svg><div><b>Phone</b><span>+987 654 3210</span></div></div>
    <div class="contact-row"><svg width="16" height="12" viewBox="0 0 16 12"><rect width="16" height="12" fill="#1fc2b5"/><path d="M1 1l7 6 7-6" fill="none" stroke="#fff" stroke-width="1.4"/></svg><div><b>Email</b><span>info@veltara.com</span></div></div>
  </div>
  <div class="abs bottom-bar">
    <p>Copyright © 2022 Veltara. All Rights Reserved.</p>
    <div class="socials"><span></span><span></span><span></span></div>
  </div>
</footer>

</body>
</html>
```